Structural Engineering Business Card

Brookvane Drafting does residential house plans for clients in Central Florida. Would like simple but elegant business card that is appropriate for a house plan engineering company. Prefer black business card with black/white them but open to other shades of blue. I uploaded a sample card that I came across that looked good but please come up with your own creative designs.

Contact Information for Business Card

Name, Title, Phone, Email, Address, website

```html
<!DOCTYPE html>
<html lang="en">
<head>
<meta charset="UTF-8">
<title>Brookvane Drafting — Business Card</title>
<link href="https://fonts.googleapis.com/css2?family=Montserrat:wght@400;500;800&display=swap" rel="stylesheet">
<style>
  :root {
    --backdrop: #cfcfcf;
    --ink: #0a0a0a;
    --paper: #ffffff;
    --muted: #6b6b6b;
    --wave-shade: #5e5e5e;
  }
  html, body {
    margin: 0;
    padding: 0;
    width: 1200px;
    height: 1200px;
    overflow: hidden;
    background: var(--backdrop);
    font-family: "Montserrat", Arial, sans-serif;
  }
  .canvas {
    position: relative;
    width: 1200px;
    height: 1200px;
  }
  .card {
    position: absolute;
    left: 250px;
    width: 700px;
    height: 400px;
    overflow: hidden;
    box-shadow: 0 18px 40px rgba(0,0,0,0.18);
  }
  .card-front { top: 150px; background: var(--paper); }
  .card-back  { top: 650px; background: var(--ink); }

  .wave { position: absolute; inset: 0; }

  .holder {
    position: absolute;
    left: 44px;
    top: 42px;
  }
  .holder-name {
    margin: 0;
    font-weight: 800;
    font-size: 26px;
    letter-spacing: 0.5px;
    color: var(--ink);
  }
  .holder-title {
    margin: 2px 0 0;
    font-weight: 400;
    font-size: 18px;
    color: var(--muted);
  }

  .brand {
    position: absolute;
    display: flex;
    align-items: center;
    gap: 12px;
    font-weight: 800;
    white-space: nowrap;
  }
  .brand-mark { display: block; }
  .card-front .brand {
    right: 44px;
    top: 140px;
    font-size: 30px;
    color: var(--ink);
  }
  .card-front .brand-mark { width: 22px; height: 22px; background: var(--ink); }
  .card-back .brand {
    left: 50%;
    top: 50%;
    transform: translate(-50%, -50%);
    font-size: 50px;
    color: var(--paper);
  }
  .card-back .brand-mark { width: 34px; height: 34px; background: var(--paper); }

  .contact {
    position: absolute;
    left: 44px;
    top: 196px;
    margin: 0;
    padding: 0;
    list-style: none;
    color: var(--paper);
    font-size: 18px;
    font-weight: 500;
    line-height: 1.5;
  }
  .contact li { display: flex; align-items: center; gap: 10px; }
  .contact .address { display: block; padding-left: 26px; margin-bottom: 2px; }
  .contact svg { width: 16px; height: 16px; flex: none; }
</style>
</head>
<body>
<div class="canvas">

  <section class="card card-front">
    <svg class="wave" viewBox="0 0 700 400" preserveAspectRatio="none" aria-hidden="true">
      <path d="M0,120 C170,110 270,170 350,260 C420,340 470,390 590,400 L570,400 C470,392 420,345 345,270 C265,185 170,125 0,128 Z" fill="var(--wave-shade)"/>
      <path d="M0,128 C170,125 265,185 345,270 C410,340 460,388 560,400 L0,400 Z" fill="var(--ink)"/>
    </svg>

    <div class="holder">
      <h1 class="holder-name">DORIAN VALE</h1>
      <p class="holder-title">Owner</p>
    </div>

    <div class="brand"><span class="brand-mark"></span>Brookvane Drafting</div>

    <ul class="contact">
      <li class="address">52 Palmetto Row<br>Lakeview, FL 32803</li>
      <li>
        <svg viewBox="0 0 16 16"><path d="M4 1.5l2.2 3-1.3 1.6c.8 1.8 2.2 3.2 4 4l1.6-1.3 3 2.2-1.2 2.6C6.8 13.4 2.6 9.2 1.4 3.7z" fill="currentColor"/></svg>
        (555) 014-2290
      </li>
      <li>
        <svg viewBox="0 0 16 16"><rect x="1" y="3" width="14" height="10" rx="1" fill="currentColor"/><path d="M1.5 3.8L8 9l6.5-5.2" stroke="var(--ink)" stroke-width="1.3" fill="none"/></svg>
        studio@brookvane.com
      </li>
      <li>
        <svg viewBox="0 0 16 16"><circle cx="8" cy="8" r="6.5" fill="none" stroke="currentColor" stroke-width="1.4"/><ellipse cx="8" cy="8" rx="2.8" ry="6.5" fill="none" stroke="currentColor" stroke-width="1.2"/><path d="M1.5 8h13" stroke="currentColor" stroke-width="1.2"/></svg>
        www.brookvane.com
      </li>
    </ul>
  </section>

  <section class="card card-back">
    <div class="brand"><span class="brand-mark"></span>Brookvane Drafting</div>
  </section>

</div>
</body>
</html>
```